Business Card Design Project

I need a business card design for an Organic drive thru coffee kiosk. We will serve organic coffee, teas & smoothies and will serve healthy breakfast food/snacks for people on the go.
I want the card to have 2-3 colors max (earthy colors like browns, greens and so on).
I have attached the logo I want used and would love to play off the theme of "balance."
Include:
Sun-Leaf Coffee
address: 3712 Pelwin Ct. Raleigh, NC 27699
phone: 919-555-0143
website: www.sun-leaf.com (website is not up yet but still include it on card)
email: Dorothy@sun-leaf.com
I want one of the following sayings somewhere on the card (the front or back is fine):
"Eat & Sip Bright, on the run!"
"Break the fast with Sun-Leaf"
Maybe on the back list what we offer:
-Organic coffee, espresso & tea
-Blendora smoothies & protein shakes
-Zippy Tonic (100% fresh local fruit and veggies)
-Vital Nibbles
College age to 55
Business

```html
<!DOCTYPE html>
<html lang="en">
<head>
<meta charset="utf-8">
<title>Sun-Leaf Coffee Business Card</title>
<link rel="stylesheet" href="https://fonts.googleapis.com/css2?family=Source+Sans+3:wght@400;600&display=swap">
<style>
  :root {
    --page: #efeee9;
    --card: #b4ae9d;
    --panel: #ecebe3;
    --ink: #3a1f14;
    --brand: #5a2a1a;
    --accent: #6f9a2c;
    --white: #ffffff;
  }
  * { margin: 0; padding: 0; box-sizing: border-box; }
  html, body { width: 1200px; height: 1200px; overflow: hidden; }
  body {
    background: var(--page);
    font-family: "Source Sans 3", "Myriad Pro", Arial, sans-serif;
    display: flex;
    flex-direction: column;
    align-items: center;
    justify-content: center;
    gap: 60px;
  }
  .card {
    position: relative;
    width: 840px;
    height: 480px;
    background: var(--card);
    box-shadow: 0 6px 18px rgba(0,0,0,0.18);
    overflow: hidden;
  }
  .logo-panel { position: absolute; top: 0; }
  .logo-panel svg { display: block; }
  .logo-panel .brand {
    position: absolute;
    left: 0; right: 0;
    display: flex;
    align-items: center;
    justify-content: center;
    gap: 12px;
    color: var(--brand);
    font-weight: 600;
    font-size: 40px;
    letter-spacing: 0.5px;
  }
  .brand .dot {
    width: 34px; height: 34px;
    border-radius: 50%;
    background: var(--brand);
  }
  .rule {
    position: absolute;
    height: 3px;
    background: var(--accent);
  }

  /* front */
  .front .logo-panel { left: 0; }
  .front .brand { top: 92px; }
  .contact {
    position: absolute;
    right: 70px;
    top: 178px;
    text-align: right;
    color: var(--ink);
    font-size: 30px;
    font-style: normal;
    line-height: 1.22;
  }
  .front .rule { left: 360px; right: 70px; top: 378px; }
  .website {
    position: absolute;
    right: 70px;
    top: 388px;
    color: var(--white);
    font-size: 40px;
  }

  /* back */
  .back .logo-panel { right: 0; }
  .back .brand { top: 110px; font-size: 34px; gap: 10px; }
  .back .brand .dot { width: 28px; height: 28px; }
  .offer-list {
    position: absolute;
    left: 90px;
    top: 70px;
    list-style: none;
    color: var(--ink);
    font-size: 29px;
    line-height: 1.2;
  }
  .back .rule { left: 270px; right: 300px; top: 320px; }
  .tagline {
    position: absolute;
    right: 60px;
    top: 338px;
    color: var(--white);
    font-size: 44px;
  }
</style>
</head>
<body>

<section class="card front">
  <div class="logo-panel">
    <svg width="340" height="300" viewBox="0 0 340 300" aria-hidden="true">
      <path fill="var(--panel)" d="M0 0 H340 V230
        A34 34 0 0 1 272 230 A34 34 0 0 1 204 230 A34 34 0 0 1 136 230
        A34 34 0 0 1 68 230 A34 34 0 0 1 0 230 Z"/>
    </svg>
    <div class="brand"><span class="dot"></span>Sun-Leaf</div>
  </div>
  <address class="contact">
    3712 Pelwin Ct. Raleigh,<br>
    NC 27699<br>
    919-555-0143<br>
    Dorothy@sun-leaf.com
  </address>
  <div class="rule"></div>
  <div class="website">www.sun-leaf.com</div>
</section>

<section class="card back">
  <div class="logo-panel">
    <svg width="240" height="300" viewBox="0 0 240 300" aria-hidden="true">
      <path fill="var(--panel)" d="M0 0 H240 V250
        A30 30 0 0 1 180 250 A30 30 0 0 1 120 250
        A30 30 0 0 1 60 250 A30 30 0 0 1 0 250 Z"/>
    </svg>
    <div class="brand"><span class="dot"></span>Sun-Leaf</div>
  </div>
  <ul class="offer-list">
    <li>-Organic coffee, espresso &amp; tea</li>
    <li>-Blendora smoothies &amp; protein shakes</li>
    <li>-Zippy Tonic</li>
    <li>&nbsp;(100% fresh local fruit and veggies)</li>
    <li>-Vital Nibbles</li>
  </ul>
  <div class="rule"></div>
  <div class="tagline">Eat &amp; Sip Bright, on the run!</div>
</section>

</body>
</html>
```